Business Card Design - Photographer

I am a landscape photographer and I require a business card design. 

I require two designs:
1)  a double sided business card
 and
b)  a single sided business card 

The single sided design can either be the same as the double sided (with just one side having all the information)....or it can be an entire new design. Its up to you.

My corporate colours are (CMYK):

Blue   69, 32, 0, 0
Grey  72,  64,  47,  31
Green  32,  2,  91,  0
Yellow   0, 19, 92, 0
Orange  0, 39, 75, 0

Colour space in final file should be in CMYK.

The details that need to be included on the card:

- Use the provided Logo
- Name: Wiktor Baranowski
- Email:   sales@vistalumeworks.com.au
- Website:    vistalumeworks.com.au
- Twitter:    twitter.com/vistalumeworks
- Facebook:   facebook.com/vistalumeworks
- Mobile  0417 539 662

Please use the attached template to design the logo to the specified size, including the marked bleed lines. I have also attached my logo in PNG (transparent background) and ai format for you to use.

The final file should be:
- Photoshop version with layers so I can edit the name/text etc. All non vector files should be high resolution at 1039 x 697 pixels at 300 dpi.

I also require a file as:
- Vector based PDF

Anyway questions please contact me.

Thank you

Industry/Entity Type

Landscape

Logo styles of interest
Pictorial/Combination Logo
Abstract Logo
Wordmark Logo
Lettermark Logo
Requirements
Must have
• The details that need to be included on the card:

- Use the provided Logo
- Name: Wiktor Baranowski
- Email: sales@vistalumeworks.com.au
- Website: vistalumeworks.com.au
- Twitter: twitter.com/vistalumeworks
- Facebook: facebook.com/vistalumeworks
- Mobile 0417 539 662

```html
<!DOCTYPE html>
<html lang="en">
<head>
<meta charset="utf-8">
<title>Vistalume Works – Business Card</title>
<link rel="stylesheet" href="https://fonts.googleapis.com/css2?family=Cinzel:wght@500&family=Open+Sans:wght@400;600&display=swap">
<style>
  :root {
    --page: #e9e7e4;
    --card-white: #ffffff;
    --slate: #3d4356;
    --accent-blue: #3a8fcf;
    --ink: #3d4356;
    --text-light: #ffffff;
    --twitter-chip: #5fb4e6;
    --facebook-chip: #4a6aa8;
    --shadow: rgba(0, 0, 0, 0.18);
  }
  * { box-sizing: border-box; margin: 0; padding: 0; }
  html, body {
    width: 1200px; height: 758px; overflow: hidden;
    background: var(--page);
  }
  .stage { position: relative; width: 1200px; height: 758px; }
  .card {
    position: absolute; top: 224px;
    width: 520px; height: 310px;
    border-radius: 26px; overflow: hidden;
    box-shadow: 0 6px 18px var(--shadow);
  }

  /* front – carries every detail, so it also serves as the single-sided card */
  .card-front { left: 50px; background: var(--card-white); }
  .brand-block {
    position: absolute; left: 0; top: 0; width: 270px; height: 310px;
    display: flex; flex-direction: column; align-items: center; justify-content: center; gap: 18px;
  }
  .brand-mark { width: 74px; height: 74px; border-radius: 50%; background: var(--slate); }
  .brand-name {
    font-family: "Cinzel", serif; font-weight: 500; font-size: 21px;
    letter-spacing: 0.5px; color: var(--ink);
  }
  .contact-panel {
    position: absolute; left: 270px; top: 36px; width: 250px; height: 238px;
    background: var(--slate);
  }
  .web-strip {
    position: absolute; left: 0; top: 0; width: 20px; height: 100%;
    background: var(--accent-blue);
    display: flex; align-items: center; justify-content: center;
  }
  .web-strip span {
    transform: rotate(-90deg); white-space: nowrap;
    font-family: "Open Sans", sans-serif; font-size: 11.5px; color: var(--text-light);
  }
  .holder-name {
    position: absolute; left: 38px; top: 22px;
    font-family: "Open Sans", sans-serif; font-weight: 600; font-size: 14px;
    color: var(--text-light); white-space: nowrap;
  }
  .contact-list {
    position: absolute; left: 38px; top: 52px; list-style: none;
    font-family: "Open Sans", sans-serif; font-size: 12.5px; color: var(--text-light);
  }
  .contact-list li { display: flex; align-items: center; gap: 6px; height: 20px; white-space: nowrap; }
  .contact-list svg { width: 10px; height: 10px; flex: none; }
  .address {
    position: absolute; left: 42px; top: 152px;
    font-family: "Open Sans", sans-serif; font-size: 12.5px; line-height: 20px; color: var(--text-light);
  }

  /* back */
  .card-back {
    left: 630px; background: var(--slate);
    display: flex; flex-direction: column; align-items: center; justify-content: center; gap: 16px;
  }
  .back-mark { width: 120px; height: 120px; border-radius: 50%; background: var(--text-light); }
  .back-name {
    font-family: "Cinzel", serif; font-weight: 500; font-size: 18px; color: var(--text-light);
  }
  .back-web {
    font-family: "Cinzel", serif; font-weight: 500; font-size: 14px;
    letter-spacing: 0.5px; color: var(--text-light);
  }
</style>
</head>
<body>
<main class="stage">
  <section class="card card-front" aria-label="Card front, single-sided version">
    <div class="brand-block">
      <div class="brand-mark"></div>
      <div class="brand-name">VISTALUME WORKS</div>
    </div>
    <div class="contact-panel">
      <div class="web-strip"><span>www.vistalumeworks.com.au</span></div>
      <p class="holder-name">Wiktor Baranowski</p>
      <ul class="contact-list">
        <li>
          <svg viewBox="0 0 10 10"><rect x="2.5" y="0.5" width="5" height="9" rx="1" fill="none" stroke="#fff" stroke-width="1.2"/></svg>
          0417 539 662
        </li>
        <li>
          <svg viewBox="0 0 10 10"><rect x="0.5" y="2" width="9" height="6.5" fill="#fff"/><path d="M0.5 2 L5 5.5 L9.5 2" fill="none" stroke="#3d4356" stroke-width="0.9"/></svg>
          sales@vistalumeworks.com.au
        </li>
        <li>
          <svg viewBox="0 0 10 10"><rect width="10" height="10" rx="1.5" fill="var(--twitter-chip)"/></svg>
          vistalumeworks
        </li>
        <li>
          <svg viewBox="0 0 10 10"><rect width="10" height="10" rx="1.5" fill="var(--facebook-chip)"/></svg>
          vistalumeworks
        </li>
      </ul>
      <p class="address">00, Complex name, state<br>city 0020</p>
    </div>
  </section>

  <section class="card card-back" aria-label="Card back">
    <div class="back-mark"></div>
    <div class="back-name">VISTALUME WORKS</div>
    <div class="back-web">WWW.VISTALUMEWORKS.COM.AU</div>
  </section>
</main>
</body>
</html>
```